Law Firm Logo and Business Card Design

I need a logo and business card design for a law firm I just started. The law firm is named Law Office of Doreen K. Ashworth, LLC. The type of law I practice is Family Law, which includes divorce, custody, child support, alimony, property division, and the like. I would like to see designs that are unique and modern, yet sophisticated. I would also like to use the logo/design for my letterhead. I am not opposed to using some form of the scales of justice although I'd like something other than the typical, old fashioned scales of justice. I had considered a house made out of puzzle pieces with one puzzle piece pulled away from the others, with the logo text reading "Helping your family move forward, one step at a time." However, I don't want that particular design to look juvenile. I also would not be opposed to some form of my initials on the logo -- my initials are DKA. I am open to any other ideas you may have. I would like to see raised designs/lettering, and/or metallic finish. I like the colors black, white, gold, silver, and/or teal.

Industry/Entity Type

Law Firm

```html
<!DOCTYPE html>
<html lang="en">
<head>
<meta charset="utf-8">
<title>Law Office of Doreen K. Ashworth, LLC — Business Card</title>
<link rel="stylesheet" href="https://fonts.googleapis.com/css2?family=Open+Sans:wght@400;700&family=Roboto+Condensed:ital,wght@1,400&display=swap">
<style>
  :root {
    --backdrop: #e3e3e3;
    --gold: #d8b46a;
    --ink: #1a1a1a;
    --paper-white: #ffffff;
  }
  * { box-sizing: border-box; margin: 0; padding: 0; }
  html, body {
    width: 1200px;
    height: 900px;
    overflow: hidden;
    background: var(--backdrop);
  }
  .canvas {
    width: 1200px;
    height: 900px;
    display: flex;
    align-items: center;
    justify-content: center;
    gap: 50px;
  }
  .card {
    width: 525px;
    height: 300px;
    padding: 22px;
    box-shadow: 0 6px 18px rgba(0,0,0,0.12);
  }
  .card-inner {
    width: 100%;
    height: 100%;
  }

  /* Front */
  .card--front { background: var(--gold); }
  .card--front .card-inner {
    background: var(--ink);
    display: flex;
    flex-direction: column;
    align-items: center;
    justify-content: center;
    color: var(--paper-white);
    text-align: center;
  }
  .brand-mark {
    display: flex;
    align-items: center;
    gap: 12px;
    margin-bottom: 8px;
  }
  .brand-mark__dot {
    width: 60px;
    height: 60px;
    border-radius: 50%;
    background: var(--gold);
  }
  .brand-mark__name {
    font-family: "Open Sans", sans-serif;
    font-weight: 700;
    font-size: 30px;
    letter-spacing: 2px;
    color: var(--paper-white);
  }
  .tagline {
    font-family: "Roboto Condensed", sans-serif;
    font-style: italic;
    font-size: 11px;
    color: var(--paper-white);
    margin-bottom: 10px;
  }
  .firm-name {
    font-family: "Open Sans", sans-serif;
    font-weight: 700;
    font-size: 25px;
    line-height: 1.2;
  }

  /* Back */
  .card--back { background: var(--ink); padding: 18px; }
  .card--back .card-inner {
    background: var(--gold);
    padding: 22px 30px;
    color: var(--ink);
  }
  .card--back .firm-name {
    font-size: 19px;
    line-height: 1.15;
    text-align: center;
    margin-bottom: 12px;
  }
  .contact-list {
    list-style: none;
    margin-left: 120px;
    padding-left: 16px;
    border-left: 1px solid var(--ink);
    font-family: "Open Sans", sans-serif;
    font-size: 14px;
    line-height: 1.6;
  }
</style>
</head>
<body>
<main class="canvas">
  <section class="card card--front" aria-label="Business card front">
    <div class="card-inner">
      <div class="brand-mark">
        <span class="brand-mark__dot" aria-hidden="true"></span>
        <span class="brand-mark__name">DKA</span>
      </div>
      <p class="tagline">"Helping your family move forward, one step at a time."</p>
      <h1 class="firm-name">Law Office of<br>Doreen K. Ashworth, LLC.</h1>
    </div>
  </section>

  <section class="card card--back" aria-label="Business card back">
    <div class="card-inner">
      <h2 class="firm-name">Law Office of<br>Doreen K. Ashworth, LLC.</h2>
      <ul class="contact-list">
        <li>2140 Harbor Point Blvd.</li>
        <li>Bayview, MD 20614</li>
        <li>(410) 555-0182</li>
        <li>info@ashworthfamilylaw.com</li>
        <li>www.ashworthfamilylaw.com</li>
      </ul>
    </div>
  </section>
</main>
</body>
</html>
```